VOMRA Pty Ltd Business Card

Looking for a simple yet eye-catching double-sided business card design using my company logo on one side and contact details on the other.

Target Market(s)

Government

Industry/Entity Type

Communication Systems Engineering

Contact Information for Business Card

VOMRA Pty Ltd

Requirements
Nice to have
• Would be great to have a QR code so details can be scanned into contacts

```html
<!DOCTYPE html>
<html lang="en">
<head>
<meta charset="utf-8">
<title>VOMRA Pty Ltd Business Card</title>
<link rel="stylesheet" href="https://fonts.googleapis.com/css2?family=Montserrat:wght@400;700&display=swap">
<style>
  :root {
    --slate: #37424a;
    --ink: #111416;
    --paper: #ffffff;
    --backdrop: #e3e3e1;
    --text: #2b3237;
  }
  * { margin: 0; padding: 0; box-sizing: border-box; }
  html, body { width: 1200px; height: 801px; overflow: hidden; }
  body {
    background: var(--backdrop);
    font-family: "Montserrat", sans-serif;
    color: var(--text);
    position: relative;
  }
  .card {
    position: absolute;
    top: 245px;
    width: 540px;
    height: 310px;
    background: var(--paper);
    border-radius: 22px;
    overflow: hidden;
    box-shadow: 0 10px 30px rgba(0,0,0,0.18);
  }
  .card--details { left: 40px; }
  .card--brand { left: 620px; }
  .card__bands { position: absolute; inset: 0; }
  .brand-name {
    position: absolute;
    font-weight: 700;
    color: var(--slate);
    letter-spacing: 2px;
    line-height: 1;
  }
  .card--details .brand-name { left: 92px; top: 132px; font-size: 44px; }
  .card--brand .brand-name {
    left: 0; right: 0; top: 115px;
    text-align: center; font-size: 82px; letter-spacing: 4px;
  }
  .divider {
    position: absolute;
    left: 300px; top: 62px;
    width: 1px; height: 188px;
    background: var(--slate);
  }
  .contact {
    position: absolute;
    left: 318px; top: 66px;
    width: 190px;
  }
  .contact__name { font-size: 18px; font-weight: 700; color: var(--slate); letter-spacing: 0.5px; }
  .contact__role { font-size: 12.5px; margin-top: 2px; }
  .contact__list { list-style: none; margin-top: 16px; font-size: 12.5px; }
  .contact__list li { display: flex; align-items: center; gap: 7px; height: 20px; }
  .contact__list svg { width: 12px; height: 12px; flex: none; fill: var(--slate); }
  .contact__address { margin-top: 14px; font-size: 12.5px; line-height: 1.45; }
</style>
</head>
<body>

<section class="card card--details" aria-label="Contact side">
  <svg class="card__bands" viewBox="0 0 540 310" aria-hidden="true">
    <path d="M0 0 H58 Q10 155 58 310 H0 Z" fill="var(--slate)"/>
    <path d="M66 0 Q18 155 66 310" fill="none" stroke="var(--ink)" stroke-width="3"/>
    <path d="M540 0 H482 Q530 155 482 310 H540 Z" fill="var(--slate)"/>
    <path d="M474 0 Q522 155 474 310" fill="none" stroke="var(--ink)" stroke-width="3"/>
  </svg>

  <div class="brand-name">VOMRA</div>
  <div class="divider"></div>

  <div class="contact">
    <div class="contact__name">DANIEL HART</div>
    <div class="contact__role">Managing Director</div>
    <ul class="contact__list">
      <li>
        <svg viewBox="0 0 24 24"><path d="M6.6 10.8a15 15 0 0 0 6.6 6.6l2.2-2.2a1 1 0 0 1 1-.25 11.4 11.4 0 0 0 3.6.6 1 1 0 0 1 1 1V20a1 1 0 0 1-1 1A17 17 0 0 1 3 4a1 1 0 0 1 1-1h3.5a1 1 0 0 1 1 1c0 1.25.2 2.45.6 3.6a1 1 0 0 1-.25 1z"/></svg>
        100 200 300
      </li>
      <li>
        <svg viewBox="0 0 24 24"><path d="M2 5h20v14H2z M2 5l10 8 10-8" fill="var(--slate)" stroke="#fff" stroke-width="1.5"/></svg>
        admin@vomra.com.au
      </li>
      <li>
        <svg viewBox="0 0 24 24"><circle cx="12" cy="12" r="10"/><path d="M2 12h20M12 2c3 3 3 17 0 20M12 2c-3 3-3 17 0 20" fill="none" stroke="#fff" stroke-width="1.4"/></svg>
        www.vomra.com.au
      </li>
    </ul>
    <p class="contact__address">14-16 Harbour Lane Riverton<br>NSW 2099 Australia</p>
  </div>
</section>

<section class="card card--brand" aria-label="Brand side">
  <div class="brand-name">VOMRA</div>
</section>

</body>
</html>
```